Medical Learning Web Design Project

The web site will be a site for medical students. It is aimed at providing a collaborative place for students to study, learn, question each other and challenge each other with learning. The site needs to have a section on the page that is for the content and this needs to be relatively clean and clinical. The surrounding elements will be informative (for the statistics, challenge etc). There will also be a slide-out screen that allows for the social/friend elements of the site.

The colour scheme needs to be clean and clinical where appropriate, but also engaging and exciting for the social/competitive elements.
Updates

Just for clarity: The site isn't expected to be 'coded' ... it is just the layered PSD files that I need.

Also, with regards to the navigation buttons ... they will never ALL be present at the same time so don't feel the need to design all on one page, but creativity around allowing few or many on a page will be an advantage ...

Thanks

Hi,

Please note that the image uploaded has been done as a wireframe by the developers. I am looking for a more creative and engaging way of presenting that content ...

Thanks

Hi all

Thank you all for the designs so far ...!

Please have a look at the new uploaded file, I am also looking not just for a 'templated home page' but also some different layouts that are represented in these wireframes. If the various layouts represented can be condensed down into 1 or 2 page templates with appropriate colour schemes to capture the type of content on the page (as already mentioned ... social .. competitive ... learning), then that will help me live the concepts better too! The friends tab for instance I have envisaged as a slider covering the screen and then sliding back when complete ... but let me see what creativity you can give to this ...!

Many thanks

Reason: Just allowing for final tweaks ...

Target Market(s)

Medical Students

Industry/Entity Type

Medical

Requirements
Must have
• - Not cluttered appearance
- Dynamic navigation (ie. site will be developed to only show relevant navigation buttons on each page ...)
- Navigation buttons (need to be individual buttons) will be: 'Home', 'Take the tour', 'What your peers say', 'Subscriptions', 'Free Signup', 'Contact us', 'Moderation', 'Statistics', 'Competition', 'Answer Questions', 'Post Questions', 'My profile', 'Friends'
- Please also ensure it is engaging for social elements and competitive elements (perhaps slightly different design for pages focussed on each element)
- Please also ensure that there is a masculine design and feminine design that has continuity for the site but depending on gender the design can be tailored to be more appealing (that means perhaps male social design, male competitive design, female social design, female competitive design ... without loosing continuity through the site).
- Photoshop PSD format
- Pixel perfect at least 1000 pixels wide (but the design needs to allow for various monitor sizes (only desktop or laptops ... not tablets or smart phones)

```html
<!DOCTYPE html>
<html lang="en">
<head>
<meta charset="utf-8">
<title>Clinora – The Medical Peer Review</title>
<link href="https://fonts.googleapis.com/css2?family=Arimo:wght@400;700&family=PT+Sans+Narrow:wght@400;700&family=PT+Sans:wght@400;700&family=Goudy+Bookletter+1911&display=swap" rel="stylesheet">
<style>
:root{
  --red:#cc0000;
  --red-dark:#a80000;
  --navy:#123a6b;
  --navy-dark:#0d2d57;
  --blue-link:#1a5ea8;
  --grey-bg:#e7e7e7;
  --grey-light:#f4f4f4;
  --text:#333;
}
*{box-sizing:border-box;margin:0;padding:0}
html,body{width:1200px;height:1067px;overflow:hidden}
body{position:relative;background:var(--grey-bg);font-family:"Arimo",sans-serif;color:var(--text)}
.abs{position:absolute}

/* top bar */
.topbar{left:0;top:0;width:1200px;height:56px;background:var(--grey-light);border-bottom:1px solid #ddd}
.web-label{left:136px;top:13px;font-size:11px;color:#888}
.web-icons{left:249px;top:11px;display:flex;gap:2px}
.web-icons span{width:14px;height:14px;border-radius:2px;background:#8a9bb3}
.web-icons span:nth-child(6){background:#6aa84f}
.web-icons span:last-child{background:#e8882a}
.login-field{top:10px;width:169px;height:18px;background:#b9b9b9;color:#fff;font-size:11px;padding:2px 7px}
.login-btn{left:1013px;top:10px;width:52px;height:18px;background:var(--red);color:#fff;font-size:11px;text-align:center;line-height:18px}
.keep{left:669px;top:31px;font-size:10px;color:#777;display:flex;align-items:center;gap:5px}
.keep i{width:11px;height:11px;border:1px solid #aaa;background:#fff;display:block}
.forgot{left:843px;top:34px;font-size:10px;color:var(--red)}

/* header */
.header{left:0;top:57px;width:1200px;height:190px;background:linear-gradient(#f3f3f3,#e4e4e4)}
.brand{left:133px;top:86px;display:flex;align-items:center;gap:8px}
.brand-name{font-family:"Goudy Bookletter 1911",serif;font-size:46px;color:var(--navy);line-height:1}
.brand-dot{width:30px;height:30px;border-radius:50%;background:var(--red)}
.brand-tag{left:137px;top:135px;font-size:13px;color:#555;font-family:"PT Sans",sans-serif}
.quote{left:360px;top:105px;width:417px;text-align:right;font-family:"PT Sans Narrow",sans-serif;font-size:15px;color:var(--navy);line-height:18px;padding-right:14px;border-right:1px solid #ccc}
.stats-cta{left:820px;top:97px;width:243px;text-align:right;font-family:"PT Sans Narrow",sans-serif;font-size:25px;line-height:25px}
.stats-cta .top{color:var(--red)}
.stats-cta .bottom{color:var(--navy);font-weight:700}

/* navigation */
.nav-tray{left:141px;top:187px;width:928px;height:56px;background:linear-gradient(#fbfbfb,#ececec);border-radius:14px 14px 0 0;border:1px solid #dcdcdc;border-bottom:none}
.nav-rule{left:0;top:242px;width:1200px;height:6px;background:var(--navy)}
.nav-home{left:234px;top:181px;width:82px;height:62px;background:var(--navy);border-top:5px solid var(--red);color:#fff;text-align:center;font-family:"PT Sans Narrow",sans-serif;font-size:14px}
.nav-home svg{display:block;margin:8px auto 4px}
.nav-links{left:316px;top:206px;display:flex;font-family:"PT Sans Narrow",sans-serif;font-size:14px;color:var(--navy)}
.nav-links a{color:inherit;text-decoration:none;padding:0 16px;border-left:1px solid #ccc;line-height:18px}
.nav-links a:first-child{border-left:none}

/* hero */
.hero{left:0;top:248px;width:1200px;height:308px;background:linear-gradient(#e6e6e6,#f3f3f3)}
.hero-photo{left:131px;top:253px;width:370px;height:403px;border-radius:150px 150px 0 0;background:linear-gradient(160deg,#d8d4cf,#f5f5f5 55%,#e3e6ea)}
.hero-title{left:462px;top:305px;font-family:"Goudy Bookletter 1911",serif;font-weight:400;color:var(--red);font-size:42px;white-space:nowrap}
.hero-title small{font-size:24px;color:var(--navy)}
.hero-list{top:372px;list-style:none;font-family:"PT Sans",sans-serif;font-size:16px;color:#555}
.hero-list li{display:flex;align-items:center;gap:13px;height:33px}
.hero-list li::before{content:"";width:17px;height:17px;border-radius:50%;background:var(--red);box-shadow:inset 0 0 0 4px #fff,0 0 0 1px var(--red)}
.dots{left:951px;top:525px;display:flex;gap:6px}
.dots span{width:17px;height:17px;border-radius:50%;background:#f2f2f2;box-shadow:0 1px 2px rgba(0,0,0,.2)}
.dots span:first-child{background:var(--red)}

/* news band */
.band{left:0;top:556px;width:1200px;height:72px;background:var(--red)}
.band-news{left:531px;top:571px;font-size:12px;color:#fff;line-height:15px}
.share{top:580px;display:flex;gap:3px;align-items:center}
.share .btn{height:18px;padding:0 6px;background:#eef2f8;border:1px solid #c9d3e3;font-size:11px;color:var(--blue-link);line-height:16px;border-radius:2px}
.share .count{height:18px;padding:0 5px;background:#fff;border:1px solid #ccc;font-size:11px;color:#333;line-height:16px;border-radius:2px}

/* columns */
.panel{top:652px;width:308px;height:332px;background:#fff;box-shadow:0 0 6px rgba(0,0,0,.12)}
.panel-head{top:653px;width:284px;height:52px;font-family:"Goudy Bookletter 1911",serif;font-weight:400;font-size:25px;color:#fff;padding-left:16px;line-height:52px;background:var(--navy)}
.panel-head.red{background:var(--red);text-align:center;padding:0}
.author{left:143px;top:721px;display:flex;gap:8px;align-items:center}
.avatar{width:46px;height:46px;background:#f0f0f0;border:1px solid #ddd;display:flex;align-items:center;justify-content:center}
.avatar i{width:30px;height:30px;border-radius:50%;background:var(--red)}
.author b{display:block;font-size:13px;color:var(--blue-link)}
.author span{font-size:12px;font-weight:700;color:#222}
.posts{left:143px;top:773px;width:274px;list-style:none;font-size:10px;line-height:15px;color:#222}
.posts li{border-top:1px solid #ddd;padding:5px 0 6px}
.posts em{font-style:normal;color:var(--red);display:block;margin-top:2px}
.posts-foot{left:143px;top:943px;width:274px;border-top:1px solid #ddd;padding-top:7px;display:flex;justify-content:space-between;align-items:center}
.posts-foot b{font-size:16px;color:#3fb6e4}
.posts-foot span{font-size:10px;color:#222}
.video{left:460px;top:727px;width:283px;height:244px;border:1px solid #ddd;background:linear-gradient(#fafafa,#e9e9e9)}
.video-player{left:463px;top:938px;width:277px;height:28px;display:flex;align-items:center;gap:4px}
.video-player .play{width:41px;height:26px;background:#222;border-radius:3px;display:flex;align-items:center;justify-content:center}
.video-player .bar{flex:1;height:20px;background:#1b1b1b;border-radius:3px;display:flex;align-items:center;justify-content:flex-end;padding:0 8px;color:#fff;font-size:13px;font-weight:700}
.fb-page{left:786px;top:722px;display:flex;gap:10px;align-items:center}
.fb-page b{font-size:13px;color:var(--blue-link);display:block}
.fb-like{display:inline-block;font-size:10px;border:1px solid #c9d3e3;background:#eef2f8;padding:1px 5px;color:var(--blue-link);margin-right:6px}
.fb-page small{font-size:10px;color:#222}
.fb-count{left:786px;top:781px;width:254px;border-top:1px solid #d8dfea;padding-top:6px;font-size:10px;color:#333}
.faces{left:786px;top:803px;display:grid;grid-template-columns:repeat(5,47px);column-gap:5px;row-gap:3px;font-size:9px;color:#666;text-align:center}
.faces div{height:47px;background:linear-gradient(#9aa6b3,#5e6873)}
.faces div:nth-child(even){background:linear-gradient(#b89b86,#6c5a4c)}
.faces-sep{left:786px;top:923px;width:254px;border-top:1px solid #d8dfea}
.plugin{left:786px;top:959px;font-size:9px;color:#666;display:flex;gap:4px;align-items:center}
.plugin i{width:11px;height:11px;background:#3b5998;display:block}

/* footer */
.foot-band{left:0;top:973px;width:1200px;height:45px;background:var(--navy)}
.footer{left:131px;top:996px;width:938px;height:71px;background:var(--red);text-align:center;color:#fff;font-size:12px}
.footer nav{margin-top:15px}
.footer nav a{color:#fff;text-decoration:none;padding:0 7px}
.footer p{margin-top:8px;font-size:11px}
</style>
</head>
<body>

<div class="abs topbar"></div>
<div class="abs web-label">Clinora on the web:</div>
<div class="abs web-icons" aria-label="Social links"><span></span><span></span><span></span><span></span><span></span><span></span><span></span><span></span><span></span></div>
<div class="abs login-field" style="left:667px">Enter Your User Name</div>
<div class="abs login-field" style="left:841px">Enter Your Password</div>
<div class="abs login-btn">Login</div>
<div class="abs keep"><i></i>Keep my signed in</div>
<div class="abs forgot">Forgot your password?</div>

<header class="abs header"></header>
<div class="abs brand"><span class="brand-name">Clinora</span><span class="brand-dot"></span></div>
<div class="abs brand-tag">The medical peer review</div>
<div class="abs quote">"Clinora keeps me ahead of the game, constantly testing my knowledge..."<br>--- Sam, dortor in training, University of Northfield</div>
<div class="abs stats-cta"><div class="top">WHO WILL YOUR STATS</div><div class="bottom">COMPARE?</div></div>

<div class="abs nav-tray"></div>
<div class="abs nav-rule"></div>
<div class="abs nav-home">
  <svg width="20" height="20" viewBox="0 0 20 20"><path d="M7 1h6v6h6v6h-6v6H7v-6H1V7h6z" fill="#fff"/></svg>HOME
</div>
<nav class="abs nav-links">
  <a href="#">TAKE THE TOUR</a><a href="#">WHAT YOUR PEERS SAY</a><a href="#">SUBSCRIPTION PLANS</a><a href="#">FREE SIGNUP</a><a href="#">CONTACT US</a>
</nav>

<section class="abs hero"></section>
<div class="abs hero-photo" role="img" aria-label="Smiling doctor in a white coat with arms folded"></div>
<h1 class="abs hero-title">Clinora - <small>The Medical Peer Review</small></h1>
<ul class="abs hero-list" style="left:459px">
  <li>Test your medical knowledge</li>
  <li>Earn trophies as your knowledge increases</li>
  <li>Answer a vast array of medical questions</li>
  <li>Link to your friends and check their progress</li>
</ul>
<ul class="abs hero-list" style="left:843px">
  <li>Rate questions from peers</li>
  <li>Ask your own questions</li>
  <li>29.903 Questions answered!</li>
</ul>
<div class="abs dots"><span></span><span></span><span></span><span></span><span></span></div>

<div class="abs band"></div>
<div class="abs band-news">About 2 days ago:<br>Clinora is now on Friendbook. Follow us <u>Here</u>.</div>
<div class="abs share" style="left:802px"><span class="btn">Like</span><span class="count">84</span></div>
<div class="abs share" style="left:900px"><span class="btn">+1</span><span class="count">2</span></div>
<div class="abs share" style="left:970px"><span class="btn">Chirp</span><span class="count">11</span></div>

<section class="abs panel" style="left:131px"></section>
<h2 class="abs panel-head" style="left:142px">Latest Chirps</h2>
<div class="abs author"><div class="avatar"><i></i></div><div><b>Clinora</b><span>Clinora Medical Peer Review</span></div></div>
<ul class="abs posts">
  <li>Lorem ipsum dolor sit amet, consectetur adipisicing elit, sed do eiusmod tempor...<em>17-Sep-2012</em></li>
  <li>Lorem ipsum dolor sit amet, consectetur adipisicing elit, sed do eiusmod tempor...<em>17-Sep-2012</em></li>
  <li>Lorem ipsum dolor sit amet, consectetur adipisicing elit, sed do eiusmod tempor...<em>17-Sep-2012</em></li>
</ul>
<div class="abs posts-foot"><b>Chirper</b><span>Join the Conversation</span></div>

<section class="abs panel" style="left:447px"></section>
<h2 class="abs panel-head red" style="left:460px">How Clinora Works?</h2>
<div class="abs video" role="img" aria-label="Video still of a young doctor with a stethoscope"></div>
<div class="abs video-player">
  <div class="play"><svg width="12" height="14" viewBox="0 0 12 14"><path d="M1 1l10 6-10 6z" fill="#fff"/></svg></div>
  <div class="bar">reelbox</div>
</div>

<section class="abs panel" style="left:762px"></section>
<h2 class="abs panel-head" style="left:774px">Follow us on Friendbook</h2>
<div class="abs fb-page"><div class="avatar"><i></i></div><div><b>Clinora</b><span class="fb-like">Like</span><small>You like this</small></div></div>
<div class="abs fb-count">21,227 people like</div>
<div class="abs faces" role="img" aria-label="Profile photos of people who like the page">
  <div></div><div></div><div></div><div></div><div></div>
  <span>Owen</span><span>Milo</span><span>Reuben</span><span>Kit</span><span>Ewan</span>
  <div></div><div></div><div></div><div></div><div></div>
</div>
<div class="abs faces-sep"></div>
<div class="abs plugin"><i></i>Friendbook social plugin</div>

<div class="abs foot-band"></div>
<footer class="abs footer">
  <nav><a href="#">Home</a>|<a href="#">Take The Tour</a>|<a href="#">What your Peers Say</a>|<a href="#">Subscription Plans</a>|<a href="#">Free Signup</a>|<a href="#">Contact Us</a>|<a href="#">Sitemap</a></nav>
  <p>Copyright © 2012 Clinora, All rights reserved!</p>
</footer>

</body>
</html>
```